Logo + Label Design (Men’s Grooming Brand & Product Packaging)

Design a logo and 2 oz pomade label for Brel, a modern men’s grooming brand focused on clean, high-quality, natural ingredients. The design should establish a bold, masculine, minimalist identity that can later extend to products like shaving gel and body wash.

Key Requirements

Create a primary logo for “Brel” and a core label for the 2 oz pomade jar (screw-top).

Use a clean, modern style — masculine, confident, and approachable (think Dorran’s, Velta, Northfield Kit).

Design for 1–2 color screen printing on solid jar colors (white, black, or navy).

Avoid gradients, foil, or embossing. Must work in black & white.

Provide: vector logo, mockup of the 2 oz jar, color palette (CMYK/RGB/HEX), and font specs.

Winning design may lead to future projects (body wash, shave gel, skincare lines).

Font styles to use
Other font styles liked:
• We like the fonts and design concept in the attached mockup.

Requirements
Should not have
• We want to avoid too much writing or busy designs. We want to avoid having graphics/illustrations embedded in the logo if they will cause the brand to look less classy or sophisticated. We also want the design to look simple and all-American (e.g. Hollister and Vane, Pine Ledger, The KIM, etc). We’d like to give a Pellham & Royce vibe that feels classy and high end.

```html
<!DOCTYPE html>
<html lang="en">
<head>
<meta charset="utf-8">
<title>Brel Hair Pomade – Jar Labels</title>
<link rel="stylesheet" href="https://fonts.googleapis.com/css2?family=Montserrat:wght@400;600&display=swap">
<style>
  :root {
    --bg: #d3d1d2;
    --label-black: #18191b;
    --gold: #d4ad0a;
    --gold-ring: #c9a30c;
    --ink-light: #dfe2e7;
    --nut-brown: #9a6438;
  }
  * { margin: 0; padding: 0; box-sizing: border-box; }
  html, body { width: 1200px; height: 800px; overflow: hidden; }
  body { background: var(--bg); position: relative; font-family: "Montserrat", sans-serif; }

  /* Shared type */
  .brand-name { font-weight: 600; color: var(--ink-light); line-height: 1; letter-spacing: 1px; }
  .product-name { font-weight: 400; color: var(--gold); letter-spacing: 2px; text-transform: uppercase; white-space: nowrap; }
  .specs { text-align: center; color: var(--ink-light); font-weight: 400; }
  .nut-art { border-radius: 40%; background: radial-gradient(circle at 45% 45%, #c88a52, var(--nut-brown) 70%, #5b3a1e); }

  /* Side wrap label */
  .wrap-label {
    position: absolute; left: 168px; top: 420px; width: 384px; height: 180px;
    background: var(--label-black);
    border-top: 6px solid var(--gold); border-bottom: 6px solid var(--gold);
    display: flex; flex-direction: column; align-items: center; padding-top: 26px;
  }
  .wrap-label .brand-name { font-size: 54px; }
  .wrap-label .product-name { font-size: 13px; margin-top: 8px; }
  .wrap-label .specs { font-size: 8px; line-height: 12px; margin-top: 16px; }
  .wrap-label .nut-art { position: absolute; right: 36px; top: 54px; width: 44px; height: 30px; }

  /* Lid label */
  .lid-label {
    position: absolute; left: 642px; top: 193px; width: 392px; height: 392px;
    border-radius: 50%; background: var(--label-black);
    display: flex; flex-direction: column; align-items: center; padding-top: 56px;
  }
  .lid-label .ring {
    position: absolute; inset: 12px; border: 3px solid var(--gold-ring); border-radius: 50%;
  }
  .lid-label .nut-art { width: 90px; height: 58px; }
  .lid-label .brand-name { font-size: 92px; margin-top: 20px; }
  .lid-label .product-name { font-size: 20px; margin-top: 14px; }
  .lid-label .specs { font-size: 10px; line-height: 24px; margin-top: 30px; }
</style>
</head>
<body>
  <section class="wrap-label" aria-label="Jar side label">
    <span class="brand-name">Brel</span>
    <span class="product-name">Hair Pomade</span>
    <p class="specs">Medium Hold - Matte Finish<br>Net WT 2 oz (57g)</p>
    <div class="nut-art" role="img" aria-label="Argan nuts with leaf"></div>
  </section>

  <section class="lid-label" aria-label="Jar lid label">
    <div class="ring"></div>
    <div class="nut-art" role="img" aria-label="Argan nuts with leaf"></div>
    <span class="brand-name">Brel</span>
    <span class="product-name">Hair Pomade</span>
    <p class="specs">Medium Hold - Matte Finish<br>Net WT 2 oz (57g)</p>
  </section>
</body>
</html>
```